Tech business card design

We need an amazing business card design for our new business 'Pexla' a marketing tech startup based in Sydney, Australia. We provide an online marketplace for businesses to search and buy advertising media, connect with service providers and learn more about marketing. We wish to communicate 'cool tech', reliability and professionalism and design based around our logo.

Target Market(s)

Business Owners

Contact Information for Business Card

Name
Position
Email Address
Website
Phone Number

Font styles to use
Other font styles liked:
• Avenir & Avenir Next

Colors

Designer to choose colors to be used in the design.

```html
<!DOCTYPE html>
<html lang="en">
<head>
<meta charset="utf-8">
<title>Pexla Business Card</title>
<link href="https://fonts.googleapis.com/css2?family=Nunito+Sans:wght@400;600;700;900&display=swap" rel="stylesheet">
<style>
  :root {
    --navy: #13144a;
    --navy-deep: #0e0f38;
    --paper: #ffffff;
    --paper-shade: #ececec;
    --silver: #d3d4dc;
    --grey-text: #6b6b72;
    --stage: #e4e5ea;
  }
  * { margin: 0; padding: 0; box-sizing: border-box; }
  html, body {
    width: 1200px;
    height: 900px;
    overflow: hidden;
    background: var(--stage);
    font-family: "Nunito Sans", sans-serif;
  }
  .sheet {
    width: 1200px;
    height: 900px;
    display: flex;
    flex-direction: column;
    align-items: center;
    justify-content: center;
    gap: 44px;
  }
  .card {
    width: 700px;
    height: 400px;
    position: relative;
    box-shadow: 0 10px 30px rgba(0, 0, 0, 0.18);
  }
  .card--front {
    background: linear-gradient(150deg, var(--paper) 55%, var(--paper-shade) 100%);
  }
  .card--back {
    background: linear-gradient(160deg, var(--navy) 0%, var(--navy-deep) 100%);
  }
  .brand-name {
    position: absolute;
    font-weight: 900;
    letter-spacing: -2px;
    line-height: 1;
  }
  .card--front .brand-name {
    left: 40px;
    top: 26px;
    font-size: 128px;
    color: var(--navy);
  }
  .card--back .brand-name {
    left: 50%;
    top: 50%;
    transform: translate(-50%, -55%);
    font-size: 150px;
    color: var(--silver);
  }
  .contact {
    position: absolute;
    left: 372px;
    top: 220px;
    color: var(--navy);
  }
  .contact__name {
    font-size: 22px;
    font-weight: 600;
    letter-spacing: 0.5px;
    text-transform: uppercase;
  }
  .contact__role {
    font-size: 15px;
    color: var(--grey-text);
    margin-bottom: 12px;
  }
  .contact__address {
    font-size: 15px;
    color: var(--grey-text);
    line-height: 1.35;
    margin-bottom: 10px;
  }
  .contact__list {
    display: grid;
    grid-template-columns: 58px 16px auto;
    font-size: 15px;
    line-height: 1.4;
  }
  .contact__label { font-weight: 700; }
  .contact__value { color: var(--grey-text); }
</style>
</head>
<body>
  <main class="sheet">
    <section class="card card--front" aria-label="Card front">
      <div class="brand-name">pexla</div>
      <div class="contact">
        <div class="contact__name">Daniel Hart</div>
        <div class="contact__role">Director</div>
        <div class="contact__address">218 Marlow Lane<br>Sydney, NSW 2000</div>
        <div class="contact__list">
          <span class="contact__label">Phone</span><span>:</span><span class="contact__value">+61 2 5550 1834</span>
          <span class="contact__label">Email</span><span>:</span><span class="contact__value">info@pexla.com</span>
          <span class="contact__label">Web</span><span>:</span><span class="contact__value">www.pexla.com</span>
        </div>
      </div>
    </section>
    <section class="card card--back" aria-label="Card back">
      <div class="brand-name">pexla</div>
    </section>
  </main>
</body>
</html>
```